BOLD & MINIMALIST DESIGN NEEDED

We want a very bold but minimalistic business card design that is impactful and utilizes both sides of the business card. Our current logo is included for your use.

We want bold fonts and good use of negative space. We don't want the logo to overpower the design.

Target Market(s)

Professionals who are building new commercial buildings.

Industry/Entity Type

Construction

Contact Information for Business Card

Name, Title, email, office phone, cell phone, website

Font styles to use
Serif
Sans Serif

Requirements
Must have
• Bold design!

```html
<!DOCTYPE html>
<html lang="en">
<head>
<meta charset="utf-8">
<title>Northridge Design + Build — Business Card</title>
<link href="https://fonts.googleapis.com/css2?family=Montserrat:wght@500;800&family=Roboto:wght@400;500&display=swap" rel="stylesheet">
<style>
  :root {
    --bg: #d2d2d2;
    --card: #1a2800;
    --card-edge: #8cc63f;
    --lime: #7fbf2a;
    --lime-soft: #a6d86a;
    --white: #ffffff;
    --ink: #0b0d0f;
  }
  * { box-sizing: border-box; margin: 0; padding: 0; }
  html, body { width: 1200px; height: 802px; overflow: hidden; }
  body {
    background: var(--bg);
    font-family: "Roboto", Arial, sans-serif;
    color: var(--white);
    position: relative;
  }
  .card {
    position: absolute;
    width: 540px;
    height: 310px;
    background: var(--card);
    border-radius: 18px;
    overflow: hidden;
    box-shadow: 0 14px 30px rgba(0,0,0,.35);
  }
  .card--front { left: 40px; top: 246px; border-bottom: 6px solid var(--card-edge); }
  .card--back { left: 620px; top: 246px; }

  .wordmark { position: absolute; font-family: "Montserrat", Arial, sans-serif; font-weight: 800; color: var(--white); }
  .wordmark__name { display: block; letter-spacing: .5px; line-height: 1; }
  .wordmark__tag { display: block; font-weight: 800; letter-spacing: 6px; line-height: 1; margin-top: 6px; }
  .wordmark__square { position: absolute; background: var(--lime); }

  .card--front .wordmark { right: 34px; top: 40px; }
  .card--front .wordmark__name { font-size: 30px; }
  .card--front .wordmark__tag { font-size: 11px; text-align: right; }
  .card--front .wordmark__square { width: 16px; height: 16px; left: -26px; top: 8px; }

  .divider { position: absolute; left: 34px; right: 34px; height: 1px; background: var(--lime); }
  .divider--top { top: 128px; }

  .address { position: absolute; right: 34px; top: 144px; text-align: right; font-size: 14px; line-height: 1.35; }

  .person { position: absolute; left: 34px; top: 150px; }
  .person__name { font-family: "Montserrat", Arial, sans-serif; font-weight: 800; font-size: 24px; color: var(--lime); letter-spacing: .3px; }
  .person__title { font-size: 15px; margin-top: 2px; }
  .person__rule { width: 220px; height: 1px; background: var(--lime); margin: 10px 0 8px; }

  .contacts { list-style: none; font-size: 13px; line-height: 1.5; }
  .contacts li { display: flex; align-items: center; gap: 8px; }
  .contacts svg { width: 12px; height: 12px; flex: none; }

  .card--back .wordmark { left: 50px; top: 124px; }
  .card--back .wordmark__name { font-size: 40px; }
  .card--back .wordmark__tag { font-size: 13px; letter-spacing: 8px; margin-top: 8px; }
  .card--back .wordmark__square { width: 22px; height: 22px; left: 0; top: -36px; }
</style>
</head>
<body>

  <section class="card card--front" aria-label="Card front">
    <div class="wordmark">
      <span class="wordmark__square"></span>
      <span class="wordmark__name">NORTHRIDGE</span>
      <span class="wordmark__tag">DESIGN + BUILD</span>
    </div>
    <div class="divider divider--top"></div>
    <p class="address">4410 Harbor Ridge Blvd<br>2B-C,FL 32001</p>

    <div class="person">
      <h1 class="person__name">MARCUS BELL</h1>
      <p class="person__title">Founder &amp; CEO</p>
      <div class="person__rule"></div>
      <ul class="contacts">
        <li><svg viewBox="0 0 12 12"><path fill="#7fbf2a" d="M2 1h3l1 3-2 1a7 7 0 0 0 3 3l1-2 3 1v3c-6 0-9-3-9-9z"/></svg>012-555-014-826</li>
        <li><svg viewBox="0 0 12 12"><rect x="3" y="0.5" width="6" height="11" rx="1.2" fill="#7fbf2a"/></svg>044-555-019-237</li>
        <li><svg viewBox="0 0 12 12"><path fill="#7fbf2a" d="M1 6 11 1 8 11 6 7z"/></svg>hello@northridge.com</li>
        <li><svg viewBox="0 0 12 12"><circle cx="6" cy="6" r="5" fill="none" stroke="#7fbf2a" stroke-width="1.4"/><path d="M1 6h10M6 1c-2.5 3-2.5 7 0 10M6 1c2.5 3 2.5 7 0 10" fill="none" stroke="#7fbf2a" stroke-width="1"/></svg>www.northridge.com</li>
      </ul>
    </div>
  </section>

  <section class="card card--back" aria-label="Card back">
    <div class="wordmark">
      <span class="wordmark__square"></span>
      <span class="wordmark__name">NORTHRIDGE</span>
      <span class="wordmark__tag">DESIGN + BUILD</span>
    </div>
  </section>

</body>
</html>
```